Creation of a Valterna Flyer design

As part of the cr% 26 # 233; ation of our soci% 26 # 233; t% 26 # 233 ;, we wish to cr% 26 # 233; er a flyer pr% 26 # 233; feeling our diff% 26 # 233; annuities% 26 # 233; s business advisory services% 26 # 233; foreign% 26 # 232; res who wish to develop their activities% 26 # 233; s in Switzerland. We want a double-sided flyer that presents% 26 # 233; society% 26 # 233; t% 26 # 233; d% 26 # 39; a c% 26 # 244; t% 26 # 233; and who presents% 26 # 233; benefits of the other. We have d% 26 # 233; j% 26 # 224; made a very basic provisional flyer to be able to present our activities. We put it to you as an example.

Target Market(s)

European companies% 26 # 233; internal% 26 # 233; res% 26 # 233; es by the market% 26 # 233; Swiss

Industry/Entity Type

Business Consultant

Colors

Designer to choose colors to be used in the design.

Requirements
Must have
• Company name and contact details
A field to detail the services
Nice to have
• Some% 26 # 233; l% 26 # 233; elements that recall Switzerland and some% 26 # 233; l% 26 # 233; elements that recall c% 26 # 244; t% 26 # 233; % 26quot; business% 26quot;

```html
<!DOCTYPE html>
<html lang="en">
<head>
<meta charset="utf-8">
<title>Valterna Flyer</title>
<link rel="stylesheet" href="https://fonts.googleapis.com/css2?family=Montserrat:wght@300;400;500&display=swap">
<style>
  :root {
    --stage: #6b6c6f;
    --paper: #eeeff1;
    --paper-shade: #dfe2e6;
    --band-blue: #7f9fbd;
    --band-grey: #bcc4cd;
    --ink: #1d1d1f;
    --ink-soft: #2a2a2c;
    --footer: #7f9db8;
    --white: #ffffff;
    --mark: #050505;
  }
  * { box-sizing: border-box; margin: 0; padding: 0; }
  html, body { width: 1200px; height: 1200px; overflow: hidden; background: var(--stage); }
  .flyer {
    position: absolute; left: 168px; top: 40px;
    width: 903px; height: 1170px;
    transform: scale(0.9573); transform-origin: top left;
    background: linear-gradient(180deg, var(--paper) 0%, var(--paper-shade) 100%);
    overflow: hidden;
    font-family: "Montserrat", sans-serif;
    color: var(--ink);
  }
  .flyer__art { position: absolute; inset: 0; width: 903px; height: 1170px; }
  .brand-mark {
    position: absolute; left: 73px; top: 107px; width: 146px; height: 146px;
    background: var(--mark); border: 4px solid #c9ced4; border-radius: 30px;
    display: flex; align-items: center; justify-content: center;
  }
  .brand-mark__name { color: var(--white); font-weight: 500; font-size: 24px; letter-spacing: 0.5px; }
  .headline {
    position: absolute; left: 76px; top: 286px; width: 700px;
    font-weight: 500; font-size: 23.5px; line-height: 28.5px; color: var(--ink);
  }
  .intro {
    position: absolute; left: 76px; top: 390px; width: 800px;
    font-weight: 300; font-size: 16.8px; line-height: 21.5px; color: var(--ink-soft);
  }
  .services {
    position: absolute; left: 88px; top: 475px; width: 790px; list-style: none;
    font-weight: 300; font-size: 16.8px; line-height: 21.5px; color: var(--ink-soft);
  }
  .services__item { position: relative; padding-left: 30px; margin-bottom: 21px; }
  .services__item::before {
    content: ""; position: absolute; left: 0; top: 5px;
    width: 13px; height: 13px; border-radius: 50%; background: var(--ink);
  }
  .contact {
    position: absolute; left: 0; top: 1090px; width: 903px; height: 80px;
    background: var(--footer); color: var(--white);
    font-weight: 300; font-size: 15.5px; letter-spacing: 1.6px; line-height: 20px;
    text-align: center; padding-top: 10px;
  }
</style>
</head>
<body>
  <main class="flyer">
    <svg class="flyer__art" viewBox="0 0 903 1170" aria-hidden="false">
      <defs>
        <linearGradient id="bridge-scene" x1="0" y1="0" x2="1" y2="0.3">
          <stop offset="0" stop-color="#a23a2a"/>
          <stop offset="0.45" stop-color="#7a3d22"/>
          <stop offset="0.75" stop-color="#8da6c4"/>
          <stop offset="1" stop-color="#a9c2dc"/>
        </linearGradient>
        <linearGradient id="lake-scene" x1="0" y1="0" x2="0" y2="1">
          <stop offset="0" stop-color="#6f9a5c"/>
          <stop offset="0.35" stop-color="#9c7a5a"/>
          <stop offset="0.55" stop-color="#49b7c9"/>
          <stop offset="1" stop-color="#22c4d6"/>
        </linearGradient>
      </defs>

      <g class="top-band">
        <path d="M0,85 C150,150 250,190 420,202 C620,216 800,260 903,312 L903,0 L0,0 Z"
              fill="url(#bridge-scene)" role="img" aria-label="Photo of a flower-lined covered wooden bridge and stone water tower by a lake"/>
        <path d="M0,85 C150,150 250,190 420,202 C620,216 800,260 903,312 L903,392 C820,300 650,232 420,214 C240,200 120,150 0,110 Z"
              fill="var(--band-blue)"/>
        <path d="M0,110 C120,150 240,200 420,214 C650,232 820,300 903,392 L903,420 C820,330 640,250 420,230 C240,216 110,180 0,150 Z"
              fill="var(--band-grey)"/>
      </g>

      <g class="bottom-band">
        <path d="M0,720 C90,820 250,855 470,880 C680,905 830,930 903,985 L903,1090 L0,1090 Z"
              fill="var(--band-blue)"/>
        <path d="M0,745 C100,830 260,865 470,890 C680,915 830,945 903,1000 L903,1090 L0,1090 Z"
              fill="var(--band-grey)"/>
        <path d="M0,785 C120,860 280,885 480,902 C680,920 820,955 903,1010 L903,1090 L0,1090 Z"
              fill="url(#lake-scene)" role="img" aria-label="Photo of a lakeside castle with turrets, turquoise water and snowy mountains"/>
      </g>
    </svg>

    <div class="brand-mark"><span class="brand-mark__name">Valterna</span></div>

    <h1 class="headline">You are convinced of the potential of your product or service and you wish to focus on the Swiss market, or you want to expand your market share!</h1>

    <p class="intro">Thanks to its personalized approach and tailor made assistance, Valterna offers you the right support to develop your business activities and answers to all your questions about the Swiss market. As a partner we assist you in finding market opportunities</p>

    <ul class="services">
      <li class="services__item">By providing commercial contacts that match your target profiles;</li>
      <li class="services__item">By listing the legal and regulatory requirements specific to the Swiss market (Switzerland is not an EU member State);</li>
      <li class="services__item">By putting you in contact with private or public interlocutors in the context of an individual contact programme;</li>
      <li class="services__item">By preparing a market study that measures the potential of your product or service;</li>
      <li class="services__item">By adapting your marketing material (website, brochures, flyers, etc.) to the specific needs of the Swiss market and by translating it into German and/or French;</li>
      <li class="services__item">By organizing a promotional event that is tailored to your needs;</li>
    </ul>

    <footer class="contact">
      <p>Neuchâtel Office Valterna Sàrl Rue des Tilleuls 7 | 2017 Boudry (Neuchâtel)</p>
      <p>+41 (0)32 555 01 20 info@valterna.ch | www.valterna.ch</p>
    </footer>
  </main>
</body>
</html>
```